New Business Card Design for Manufacturing

We are an engineering/manufacturing company that offers Advanced machining/assembly/engineering services, as well as innovative products for the heavy duty engine cooling markets.

We are looking to get a new business card designed that is clean and modern looking, but still fits the wide range of technical/skilled work we do.

- We hope to use this design as the base for other design work in new Presentations, web, and print work.

Industry/Entity Type

Engineering

Contact Information for Business Card

Our preferred color of blue is (RGB) 22/71/159 but can vary slightly from that color. Our content will be our Logo and full company name (Vantrell Forge Works, Inc.), company address, name, job title, phone number with extension, cell number, fax number, website, and email address on the cards.
We'd like the full company name next to the logo, but we are open to other interpretations of that layout.
Preferably, we would like the back side to be clean with just our logo, and the front to contain all of the contact information.

Colors
2f74b4
0355a3
85abd2

Requirements
Must have
• - Logo, company name, needed content - We are open to interpretation beyond that.
• - Standard size business card.
• - Horizontal orientation.
• - Enough space for lengthy names / job titles (for example, a job title could read "Directory of Human Resources" or "V.P. of Governmental Affairs"). We need this to look clean, whether the title be short (CEO) or long (as described above).

```html
<!DOCTYPE html>
<html lang="en">
<head>
<meta charset="utf-8">
<title>Vantrell Forge Works – Business Card</title>
<link href="https://fonts.googleapis.com/css2?family=Fira+Sans:wght@400;500;700&display=swap" rel="stylesheet">
<style>
  :root {
    --brand-blue: #0355a3;
    --brand-blue-deep: #00488f;
    --brand-blue-mid: #2f74b4;
    --brand-blue-light: #85abd2;
    --paper: #e9e9e9;
    --card-white: #f4f4f4;
    --text-light: #ffffff;
  }
  * { margin: 0; padding: 0; box-sizing: border-box; }
  html, body {
    width: 1200px; height: 576px; overflow: hidden;
    background: var(--paper);
    font-family: "Fira Sans", Arial, sans-serif;
  }
  .canvas { position: relative; width: 1200px; height: 576px; }

  .card {
    position: absolute; top: 138px;
    width: 484px; height: 294px;
    border-radius: 14px; overflow: hidden;
  }

  /* Back side: logo only */
  .card-back {
    left: 82px;
    background: linear-gradient(180deg, var(--brand-blue) 0%, var(--brand-blue-deep) 100%);
  }
  .card-back .wordmark {
    position: absolute; left: 0; right: 0; top: 98px;
    text-align: center;
    font-weight: 700; font-size: 66px; letter-spacing: 2px;
    color: var(--text-light);
  }
  .card-back .web-line {
    position: absolute; left: 0; right: 0; top: 266px;
    display: flex; align-items: center; justify-content: center; gap: 12px;
    font-size: 13px; color: var(--text-light);
  }
  .card-back .rule {
    width: 52px; height: 2px; background: var(--text-light); opacity: .9;
  }

  /* Front side: contact details */
  .card-front { left: 602px; width: 480px; }
  .card-front .panel { position: absolute; inset: 0; }
  .card-front .wordmark-vertical {
    position: absolute; left: 86px; top: 142px;
    transform: translate(-50%, -50%) rotate(-90deg);
    font-weight: 700; font-size: 44px; letter-spacing: 1px;
    color: var(--brand-blue); white-space: nowrap;
  }
  .details {
    position: absolute; left: 230px; top: 36px; right: 16px;
    color: var(--text-light);
  }
  .person-name { font-weight: 500; font-size: 20px; line-height: 1.2; }
  .person-title { font-size: 11.5px; margin-top: 2px; }
  .company-name { font-weight: 500; font-size: 13px; margin-top: 44px; }
  .contact-list { list-style: none; margin-top: 6px; }
  .contact-list li {
    display: flex; align-items: center; gap: 8px;
    font-size: 12px; line-height: 16.4px;
  }
  .contact-list svg { width: 10px; height: 10px; fill: var(--text-light); flex: none; }
  .address { font-size: 12px; line-height: 16.4px; margin-top: 6px; }
</style>
</head>
<body>
<main class="canvas">

  <section class="card card-back" aria-label="Card back">
    <div class="wordmark">VANTRELL</div>
    <div class="web-line">
      <span class="rule"></span>
      <span>www.vantrellforge.com</span>
      <span class="rule"></span>
    </div>
  </section>

  <section class="card card-front" aria-label="Card front">
    <svg class="panel" viewBox="0 0 480 294" preserveAspectRatio="none" aria-hidden="true">
      <rect width="480" height="294" fill="var(--brand-blue)"/>
      <path d="M0 0 H160 Q204 140 172 294 H0 Z" fill="var(--brand-blue-light)"/>
      <path d="M0 0 H156 Q194 140 160 294 H0 Z" fill="var(--card-white)"/>
    </svg>

    <div class="wordmark-vertical">VANTRELL</div>

    <div class="details">
      <h1 class="person-name">Alden Reyes Marsh</h1>
      <p class="person-title">Managing Director</p>

      <h2 class="company-name">Vantrell Forge Works, Inc.</h2>
      <ul class="contact-list">
        <li><svg viewBox="0 0 10 10"><path d="M1 3 Q5 0 9 3 L8 4.5 L6.5 3.8 V3 H3.5 V3.8 L2 4.5 Z M2 5 H8 L9 9 H1 Z"/></svg>614-555-0182 (Ext 214)</li>
        <li><svg viewBox="0 0 10 10"><path d="M2.5 0.5 H7.5 V9.5 H2.5 Z M3.3 1.5 V7.5 H6.7 V1.5 Z"/></svg>614-555-0147</li>
        <li><svg viewBox="0 0 10 10"><path d="M2.5 0.5 H7.5 V3 H2.5 Z M0.5 3.5 H9.5 V7.5 H8 V6 H2 V7.5 H0.5 Z M2.5 6.5 H7.5 V9.5 H2.5 Z"/></svg>614-555-0190</li>
        <li><svg viewBox="0 0 10 10"><path d="M0.5 2 H9.5 V8 H0.5 Z M1 2.5 L5 5.5 L9 2.5" fill="var(--text-light)"/><path d="M1 2.6 L5 5.6 L9 2.6" fill="none" stroke="var(--brand-blue)" stroke-width=".8"/></svg>www.vantrellforge.com</li>
        <li><svg viewBox="0 0 10 10"><circle cx="5" cy="5" r="4.5"/><path d="M0.5 5 H9.5 M5 0.5 V9.5 M1.5 2.8 H8.5 M1.5 7.2 H8.5" stroke="var(--brand-blue)" stroke-width=".7" fill="none"/><ellipse cx="5" cy="5" rx="2" ry="4.5" fill="none" stroke="var(--brand-blue)" stroke-width=".7"/></svg>amarsh@vantrellforge.com</li>
      </ul>
      <p class="address">880 Kestrel Mill Rd., Dunmore Falls,<br>OH 43219</p>
    </div>
  </section>

</main>
</body>
</html>
```